Industry automation wholesale website

www.velturo.eu provides solutions for automation, building automation and digital signage.

Our products are rugged, reliable, energy saving and representative.

Scope of pages:
● welcome page
- scope of products
- applications, success stories and news
● category page
- short introduction
- sub categories
- product highlights
● product page
- short introduction
- about 3 to 4 pictures
- technical specifications: materials, dimensions
- price
- related products

Optional:
● contact page
- address
- contact form
● blog
- picture
- text
● logo
● favicon / apple touch icon

Conclusion:
● We need a professionally looking site
● Bright colors (e.g. white, grey, metalic colors, blue)

some pages we like:
http://www.prandek.de/
http://www.morvalix.de/

Target Market(s)

Our target market is the industrial sector
● Target audience: engineering and IT professionals

Industry/Entity Type

Building

Requirements
Must have
• ● only use free available fonts e.g. Lumara Type Library (http://www.lumaratype.com/webfonts)
Should not have
• ● sound
● flash

```html
<!DOCTYPE html>
<html lang="en">
<head>
<meta charset="utf-8">
<title>Velturo – analog digital measurements</title>
<link href="https://fonts.googleapis.com/css2?family=Fira+Sans:wght@300;400;500&display=swap" rel="stylesheet">
<style>
:root{
  --brand:#1f6e97;
  --brand-dark:#195a7d;
  --text:#5d5d5d;
  --head-bg:#e9e9e9;
  --hero-band:#8e8e8e;
  --line:#e3e3e3;
  --card-bg:#f7f7f7;
  --footer:#1f1f1f;
}
*{margin:0;padding:0;box-sizing:border-box}
html,body{width:1018px;height:1200px;overflow:hidden}
body{font-family:"Fira Sans",sans-serif;font-weight:300;color:var(--text);background:#fff;position:relative}
a{color:var(--brand);text-decoration:none}

.site-header{position:absolute;left:0;top:0;width:1018px;height:114px;background:var(--head-bg)}
.brand{position:absolute;left:112px;top:30px;display:flex;align-items:center;gap:8px}
.brand-name{font-size:40px;font-weight:400;color:var(--brand);line-height:1}
.brand-mark{width:12px;height:12px;background:var(--brand)}
.brand-tag{position:absolute;left:112px;top:72px;font-size:10.5px;font-weight:400;color:var(--brand)}

.search{position:absolute;left:605px;top:24px;width:189px;height:29px;background:#fff;border:1px solid #d2d2d2;font-size:9.5px;color:#999;padding:9px 11px}
.search svg{position:absolute;right:7px;top:6px}
.lang{position:absolute;left:808px;top:24px;width:99px;height:29px;background:#fff;border:1px solid #d2d2d2;font-size:11.5px;color:#777;padding:7px 10px;display:flex;align-items:center;gap:6px}
.lang .flag{width:17px;height:11px;background:#3a4d8a}
.lang .caret{margin-left:auto;border:3.5px solid transparent;border-top:4px solid var(--brand);margin-top:4px}

.main-nav{position:absolute;top:76px;left:450px;display:flex;font-size:11.5px;font-weight:400;color:#555}
.main-nav span{position:absolute;white-space:nowrap}
.main-nav .active{color:var(--brand);border-top:2px solid var(--brand);padding-top:5px;top:-7px}

.hero-band{position:absolute;left:0;top:114px;width:1018px;height:294px;background:var(--hero-band)}
.hero{position:absolute;left:111px;top:114px;width:797px;height:294px;background:linear-gradient(100deg,#4a4a4c 0%,#2c2c30 50%,#1e1f24 100%)}
.hero-arrow{position:absolute;top:122px;width:22px;height:60px;background:#cfcfcf;color:#333;font-size:18px;display:flex;align-items:center;justify-content:center}

.sidebar{position:absolute;left:110px;top:460px;width:187px;background:#f4f4f4}
.sidebar h2{background:var(--brand);color:#fff;font-size:15px;font-weight:400;padding:9px 12px;height:34px}
.sidebar ul{list-style:none;padding:4px 0 4px}
.sidebar li{font-size:10.8px;color:#666;padding:5px 0 6px 33px;border-bottom:1px solid var(--line);position:relative}
.sidebar li:last-child{border:none}
.sidebar li.has-arrow::before{content:"→";position:absolute;left:12px;color:var(--brand);font-size:10px}

.welcome{position:absolute;left:316px;top:455px;width:530px}
.welcome h1{font-size:24px;font-weight:400;color:#666}
.welcome h1 b{font-weight:400;color:var(--brand)}
.welcome p{font-size:10.6px;line-height:15.3px;margin-top:14px}
.welcome p+p{margin-top:17px}
.btn{position:absolute;left:316px;top:702px;width:99px;height:28px;background:var(--brand);color:#fff;font-size:10.5px;font-weight:400;display:flex;align-items:center;justify-content:center}

.divider{position:absolute;left:110px;top:757px;width:797px;height:2px;background:var(--line)}

.card{position:absolute;top:801px;width:253px;height:262px;background:linear-gradient(#fff,var(--card-bg));border-top:1px solid var(--line);padding:0 15px}
.card h3{height:54px;display:flex;align-items:center;font-size:14.5px;font-weight:400;color:var(--brand);line-height:18px;margin-top:2px}
.card .visual{width:223px;height:106px;margin-top:10px}
.card p{font-size:10.6px;line-height:15.3px;margin-top:25px}

.site-footer{position:absolute;left:0;top:1107px;width:1018px;height:93px;background:var(--footer);color:#eee;font-size:10.8px;font-weight:400}
.site-footer .copy{position:absolute;left:111px;top:33px}
.social{position:absolute;left:746px;top:25px;display:flex;gap:8px}
.social span{width:34px;height:34px;border-radius:4px}
</style>
</head>
<body>
<header class="site-header">
  <div class="brand"><span class="brand-name">velturo</span><span class="brand-mark"></span></div>
  <div class="brand-tag">analog digital measurements</div>
  <div class="search">Search...
    <svg width="18" height="18" viewBox="0 0 18 18"><circle cx="7" cy="7" r="5.5" fill="none" stroke="#333" stroke-width="1.6"/><line x1="11" y1="11" x2="16" y2="16" stroke="#333" stroke-width="2"/></svg>
  </div>
  <div class="lang"><span class="flag"></span>English<span class="caret"></span></div>
  <nav class="main-nav">
    <span class="active" style="left:4px">Home</span>
    <span style="left:57px">Products</span>
    <span style="left:130px">Services</span>
    <span style="left:210px">Editorial</span>
    <span style="left:289px">Contact</span>
    <span style="left:350px;top:-5px"><svg width="22" height="20" viewBox="0 0 22 20"><path d="M1 2h4l3 11h11l2-8H6" fill="none" stroke="#444" stroke-width="1.6"/><circle cx="9" cy="17" r="1.8" fill="#444"/><circle cx="17" cy="17" r="1.8" fill="#444"/></svg></span>
    <span style="left:386px">Shopping cart</span>
  </nav>
</header>

<div class="hero-band"></div>
<div class="hero" role="img" aria-label="Businessman in a dark suit touching a glowing network of connected nodes">
  <div class="hero-arrow" style="left:0">‹</div>
  <div class="hero-arrow" style="right:0;top:125px">›</div>
</div>

<aside class="sidebar">
  <h2>Range of Products</h2>
  <ul>
    <li class="has-arrow">RS422 / RS485 Converter</li>
    <li class="has-arrow">RS422 / RS485 Repeater</li>
    <li class="has-arrow">RS485 Remote IO</li>
    <li class="has-arrow">RS485 Modbus IO</li>
    <li class="has-arrow">Embedded Systems</li>
    <li class="has-arrow">PCI-Series</li>
    <li class="has-arrow">Industry PC</li>
    <li class="has-arrow">Industrial Display</li>
    <li>Din Rail Power Supply</li>
  </ul>
</aside>

<section class="welcome">
  <h1>Welcome to <b>Velturo</b></h1>
  <p>RS485 Remote IO modules are ideal to realize decentralized distributed IO units over long distances. We provide the whole product range form Remote IO Modules with RS485 Bus and Modbus RTU such as analogue IO Modules, digital IO Modules, Relay Modules and Timer / Counter Modules. Also we provide RS422 and RS485 converter to RS232, USB, TCP/IP.</p>
  <p>Velturo is your specialist partner for industrial automation. We at Velturo provide individual solutions for unitized measurement and offer the whole range of products, from interface converter over RS-485 and ModBus-Modules and to Embedded Systems and powerful Panel-PCs. Velturo is official partner of Tovra Systems. The Taiwanese specialist with the trademark KORVEX is one of the leading manufacturers of reliable industrial hardware for unitized instrumentation control and automation.</p>
</section>
<a class="btn" href="#">Learn More &gt;&gt;</a>

<div class="divider"></div>

<article class="card" style="left:110px">
  <h3>Modbus RTU / RS485 Remote IO Modules</h3>
  <div class="visual" role="img" aria-label="Rows of blue remote IO modules" style="background:linear-gradient(160deg,#9cc3e6,#3d7bb8 60%,#244f7c)"></div>
  <p>RS485 Remote IO modules are ideal to real-ize decentralized distributed IO units over long distances. <a href="#">More &gt;&gt;</a></p>
</article>
<article class="card" style="left:383px">
  <h3>Touch Panel Industry Computer</h3>
  <div class="visual" role="img" aria-label="Touch panel computer with a silver frame and blue screen" style="background:linear-gradient(135deg,#b8b8b8,#8a8a8a 30%,#4f86c4 50%,#a9c9ea)"></div>
  <p>velturo provide prestigious Touch Panel Computer for your building automation. Also we provide Human Machine. <a href="#">More &gt;&gt;</a></p>
</article>
<article class="card" style="left:655px">
  <h3>Embedded systems for industrial automation</h3>
  <div class="visual" role="img" aria-label="Fanless embedded box computer with ribbed metal case" style="background:linear-gradient(170deg,#f2f4f7,#b9bcc2 55%,#3a3c40)"></div>
  <p>Velturo is your specialist partner for indus-trial automation. We at Velturo provide individual solutions. <a href="#">More &gt;&gt;</a></p>
</article>

<footer class="site-footer">
  <div class="copy">Copyright © 2013 <a href="#" style="color:#3d8fc2">velturo</a> &nbsp;- Blog - Jobs - Disclaimer - Contact us</div>
  <div class="social">
    <span style="background:#3b5e9e"></span>
    <span style="background:#3a9ad4"></span>
    <span style="background:#d6463a"></span>
    <span style="background:#c9302a"></span>
  </div>
</footer>
</body>
</html>
```